Web Design for Webdesign company 3 page PSD

Project
---------
We need a PSD Web Design to be used in a WordPress installation.
What we would like to create is a professional looking website for a web design agency. We also need you to look for suitable stock images to be placed on these pages.
We need the design for:
Homepage
Landing page
Contact page
attached in the pages file you will find a file with more in depth details how these files should be build up.
We would like to see a desktop version and a mobile version of these pages
The website should have a 1100px width.
The mobile design should have 480px width.
The homepage should have a header slider about 450px high.
The slider is preferred full width and should have some images text and a button
Objectives
-------------
The main objective for the website is to get leads from customers in the form of a request for a quotation or a call or mail me back action. The most important action for the homepage is to link and navigate to our landing pages.
What we want to tell our visitors (our main products)
-------------------------------------------------------------------
- A website with no big investment but a monthly rate
- A successful website with no worries (a complete website, seo, hosting and a service contract for future customization is included for a monthly rate)
Color Scheme
------------
Use branding colors. You can find them in the branding.pdf file.
Additional colors:
White: #ffffff
Black: #181818
Company info
--------------
We are a starting web design / marketing agency based in The Netherlands and looking for the design of our website. Our services are (custom) webdesign, website marketing or combinations of both. Our main customer group is small business owners.
We sell websites but give the option to buy it with a lease contract.
A second product is a default website with a complete service: SEO, hosting and a service contract for a monthly rate.
Content:
-----------
If not available place Lorem Ipsum text.
There will come about 400 words of text on the landing pages
Design Competition
--------------------------
Since this is a designing competition we would like to see your creativity.
What you can expect from us is a lot of feedback 7 days a week with short response time.
You can send us the first sketchy mock ups of the homepage and we will give feedback based on these design. But we like your feedback or comments as well
Read the pages file for more in depth details how the pages should be designed

Target Market(s)
Small business owners in The Netherlands
Industry/Entity Type
It Company
Number of Pages Required
3 page
Requirements
Must have
- Homepage:
- Header slider with images, some text and a link to a custom page
- The slider should have 3 designed slides
- Landings page:
- Sidebar
- Action button for a request for a quotation
- Action button for a call me back action
- Action button for an appointment
- Contact form:
- Address details
- Contact form
Nice to have
- Homepage:
- Full width slider
- Testimonial block
- Blog items
Should not have
- Flash
- A to crowded design

```html
<!DOCTYPE html>
<html lang="en">
<head>
<meta charset="utf-8">
<title>Brightline Web Services</title>
<link href="https://fonts.googleapis.com/css2?family=Arimo:wght@400;700&family=Open+Sans:wght@400;600;700&display=swap" rel="stylesheet">
<style>
:root{
  --teal:#2a6d75;
  --green:#4d8a6c;
  --green-dark:#3f7559;
  --hero-a:#3f7d5c;
  --hero-b:#6aa884;
  --ink:#181818;
  --text:#555;
  --dark:#333333;
  --darker:#262626;
  --light:#f2f2f2;
  --line:#dcdcdc;
  --white:#ffffff;
  --muted:#b9b9b9;
  --head:"Arimo",Arial,sans-serif;
}
*{margin:0;padding:0;box-sizing:border-box}
html,body{width:807px;height:1200px;overflow:hidden;background:var(--white)}
body{font-family:"Open Sans",Arial,sans-serif;color:var(--text);position:relative}

/* header */
.site-header{position:absolute;left:0;top:0;width:807px;height:73px;background:var(--white)}
.brand{position:absolute;left:62px;top:14px;display:flex;align-items:center;gap:9px}
.brand-mark{width:44px;height:44px;border-radius:50%;background:var(--teal)}
.brand-name{color:var(--ink);font-family:var(--head);font-weight:700;font-size:15px;line-height:17px}
.brand-tagline{color:#666;font-family:var(--head);font-size:9px;line-height:12px;margin-top:2px}
.main-nav a{position:absolute;top:27px;font-family:var(--head);font-size:10.5px;font-weight:700;color:#333;text-decoration:none;height:21px;line-height:21px;letter-spacing:.2px}
.main-nav .active{left:383px;width:56px;text-align:center;background:#555;color:var(--white);border-radius:11px}

/* hero */
.hero{position:absolute;left:0;top:73px;width:807px;height:280px;background:radial-gradient(ellipse at 50% 45%,var(--hero-b) 0%,var(--hero-a) 70%,#2f6448 100%);overflow:hidden}
.hero-title{position:absolute;top:14px;width:100%;text-align:center;color:var(--white);font-family:var(--head);font-size:32px;font-weight:700}
.hero-sub{position:absolute;top:52px;width:100%;text-align:center;color:var(--white);font-family:var(--head);font-size:12.5px;font-weight:700}
.hero-devices{position:absolute;left:165px;top:88px;width:410px;height:185px;border-radius:6px;background:linear-gradient(180deg,#e9e9e9 0%,#cfcfcf 60%,#bdbdbd 100%)}
.hero-btn{position:absolute;left:600px;top:227px;width:134px;height:23px;border-radius:12px;background:var(--white);color:#222;font-family:var(--head);font-size:10.5px;font-weight:700;text-align:center;line-height:23px}
.hero svg{position:absolute;left:0;top:0}

/* call band */
.call-band{position:absolute;left:0;top:353px;width:807px;height:63px;background:var(--dark)}
.call-text{position:absolute;left:62px;top:14px;width:470px;color:var(--white);font-family:var(--head);font-size:14.5px;font-weight:700;line-height:18px}
.call-btn{position:absolute;left:590px;top:13px;width:155px;height:38px;background:var(--green);border-bottom:2px solid var(--green-dark);color:var(--white);font-family:var(--head);font-size:14.5px;font-weight:700;display:flex;align-items:center;justify-content:center;gap:10px}

/* welcome */
.welcome{position:absolute;left:0;top:416px;width:807px;height:248px;background:var(--white);border-bottom:1px solid #e2e2e2}
.welcome h2{position:absolute;left:62px;top:28px;font-family:var(--head);font-size:16px;font-weight:700;color:var(--ink)}
.welcome h2 span{color:var(--teal)}
.welcome p{position:absolute;left:62px;width:405px;font-size:8.8px;line-height:14.8px;color:var(--text)}
.btn-green{position:absolute;background:var(--green);color:var(--white);font-family:var(--head);font-size:10.5px;font-weight:700;text-align:center;border-bottom:2px solid var(--green-dark)}
.welcome-photo{position:absolute;left:474px;top:31px;width:271px;height:186px;background:linear-gradient(135deg,#2f3a4a 0%,#5a6578 40%,#d9c8b8 70%,#f1efec 100%)}

/* testimonials & blog */
.feed{position:absolute;left:0;top:665px;width:807px;height:284px;background:var(--light)}
.feed h3{position:absolute;top:31px;font-family:var(--head);font-size:15px;font-weight:400;color:var(--ink)}
.dots{position:absolute;left:353px;top:39px;display:flex;gap:3px}
.dots i{width:7px;height:7px;border-radius:50%;background:#d3d3d3}
.dots i:first-child{background:#999}
.quote{position:absolute;left:62px;top:62px;width:333px;height:121px;background:var(--white);box-shadow:0 1px 3px rgba(0,0,0,.15);padding:16px 18px;font-size:9px;line-height:15px;color:var(--text)}
.quote:after{content:"";position:absolute;left:18px;bottom:-8px;border:8px solid transparent;border-top-color:var(--white);border-bottom:0}
.avatar{position:absolute;left:62px;top:203px;width:48px;height:48px;border:3px solid var(--white);background:linear-gradient(180deg,#9aa3a8,#6d5a4c);box-shadow:0 0 2px rgba(0,0,0,.3)}
.author{position:absolute;left:122px;top:215px;font-size:10.5px;font-weight:600;color:var(--ink)}
.author small{display:block;font-size:7.5px;font-weight:400;color:#666}
.post{position:absolute;left:412px;width:333px;height:60px}
.sep{position:absolute;left:412px;width:333px;height:1px;background:var(--line)}
.date{position:absolute;left:0;top:0;width:36px;height:44px;background:var(--white);box-shadow:0 1px 2px rgba(0,0,0,.25);text-align:center;color:#333}
.date b{display:block;background:var(--green);color:var(--white);font-size:8px;line-height:11px}
.date strong{display:block;font-size:15px;line-height:17px;font-weight:600}
.date span{display:block;font-size:8px;line-height:9px;font-weight:600}
.post h4{position:absolute;left:45px;top:1px;font-size:10.5px;font-weight:700;color:var(--ink)}
.post p{position:absolute;left:45px;top:19px;width:285px;font-size:8.6px;line-height:11.5px;color:var(--text)}
.post p em{font-style:normal;color:var(--green)}

/* footer */
.site-footer{position:absolute;left:0;top:949px;width:807px;height:201px;background:var(--dark);color:var(--muted)}
.site-footer h5{position:absolute;top:36px;font-family:var(--head);font-size:10.5px;font-weight:700;color:var(--white);line-height:13px;text-transform:uppercase}
.field{position:absolute;left:62px;width:163px;height:21px;background:var(--white);border-radius:2px;font-size:8.5px;color:#888;padding-left:6px;line-height:21px}
.subscribe{position:absolute;left:62px;top:135px;width:163px;height:21px;background:#4a8a80;color:var(--white);font-family:var(--head);font-size:10px;font-weight:700;text-align:center;line-height:21px;border-radius:2px}
.links{position:absolute;left:273px;top:58px;list-style:none;font-size:8.8px;line-height:16px}
.contact-item{position:absolute;left:412px;display:flex;gap:8px;font-size:8.8px;line-height:12.5px}
.contact-item svg{flex:none;margin-top:2px}
.social{position:absolute;left:594px;display:flex;align-items:center;gap:6px;font-size:8.8px}
.social i{width:17px;height:17px;border:1.5px solid var(--muted);border-radius:50%}
.legal{position:absolute;left:0;top:1150px;width:807px;height:50px;background:var(--darker);color:#bbb;font-size:8.6px;text-align:center;line-height:15px;padding-top:10px}
</style>
</head>
<body>

<header class="site-header">
  <div class="brand">
    <div class="brand-mark"></div>
    <div>
      <div class="brand-name">Brightline Web Services</div>
      <div class="brand-tagline">Websites voor ondernemers</div>
    </div>
  </div>
  <nav class="main-nav">
    <a class="active">HOME</a>
    <a style="left:456px">LANDING</a>
    <a style="left:533px">TESTIMONIALS</a>
    <a style="left:637px">BLOG</a>
    <a style="left:696px">CONTACT</a>
  </nav>
</header>

<section class="hero">
  <h1 class="hero-title">RESPONSIVE WEB DESIGN</h1>
  <p class="hero-sub">YOUR WEBSITE READABLE ON ALL DEVICES</p>
  <div class="hero-devices" role="img" aria-label="Tablet, desktop monitor and phone showing a responsive website"></div>
  <svg width="807" height="280" viewBox="0 0 807 280" aria-hidden="true">
    <path d="M596 42 C620 50 616 72 590 76 C570 80 545 80 530 86" fill="none" stroke="#fff" stroke-width="1.3" stroke-dasharray="2 3"/>
    <path d="M534 82 L527 87 L535 90" fill="none" stroke="#fff" stroke-width="1.3"/>
    <path d="M74 112 L63 140 L74 168" fill="none" stroke="#d7e8dc" stroke-width="1.3"/>
    <path d="M733 112 L744 140 L733 168" fill="none" stroke="#d7e8dc" stroke-width="1.3"/>
  </svg>
  <div class="hero-btn">MORE INFORMATION</div>
</section>

<section class="call-band">
  <p class="call-text">A handy Lorem Ipsum Generator that helps to create dummy text for all layout needs.</p>
  <div class="call-btn">WEB DESIGN
    <svg width="20" height="20" viewBox="0 0 20 20" aria-hidden="true"><circle cx="10" cy="10" r="8.5" fill="none" stroke="#fff" stroke-width="2"/><path d="M8.5 6 L12.5 10 L8.5 14" fill="none" stroke="#fff" stroke-width="2"/></svg>
  </div>
</section>

<section class="welcome">
  <h2>WELCOME TO <span>BRIGHTLINE</span></h2>
  <p style="top:56px">Lorem ipsum dolor sit amet, cu per augue graeco cotidieque. Est ut novum laudem definiebas, no augue necessitatibus nam. Te erant dissentias appellantur cum, errem mentitum conceptam ad eum. Ad has meis adipisci, eu sed iracundia reprimique, eius perpetua vis te. Fuisset democritum scribentur ex est, mei ei viderer sapientem suscipiantur.</p>
  <p style="top:130px">Euismod appareat explicari et quo. Mei in natum errem scribentur, idque affert abhorreant et pri, ex eum torquatos adolescens. Erroribus conclusionemque cu quo. Novum putent his eu.</p>
  <div class="btn-green" style="left:62px;top:177px;width:115px;height:27px;line-height:26px">LEASE CONTRACT</div>
  <div class="welcome-photo" role="img" aria-label="Hands signing a lease contract with a pen"></div>
</section>

<section class="feed">
  <h3 style="left:62px">Client Testimonials</h3>
  <div class="dots"><i></i><i></i><i></i><i></i><i></i></div>
  <blockquote class="quote">"Lorem ipsum dolor sit amet, cu per augue graeco cotidieque. Est ut novum laudem definiebas, no augue necessitatibus nam. Te erant dissentias appellantur cum, errem mentitum conceptam ad eum. Ad has meis adipisci, eu sed iracundia reprimique, eius perpetua vis te. Fuisset democritum scribentur ex est, mei ei viderer sapientem suscipiantur."</blockquote>
  <div class="avatar" role="img" aria-label="Portrait of the client"></div>
  <div class="author">Marla Venhoek,<small>(lorem ipsum dolor amet)</small></div>

  <h3 style="left:412px">Latest Blog</h3>
  <article class="post" style="top:60px">
    <div class="date"><b>FEB</b><strong>01</strong><span>2014</span></div>
    <h4>Lorem ipsum dolor sit amet...</h4>
    <p>Lorem Ipsum is simply dummy text of the printing and typesetting industry. <em>[+]</em></p>
  </article>
  <div class="sep" style="top:120px"></div>
  <article class="post" style="top:135px">
    <div class="date"><b>FEB</b><strong>01</strong><span>2014</span></div>
    <h4>Lorem ipsum dolor sit amet...</h4>
    <p>Lorem Ipsum is simply dummy text of the printing and typesetting industry. <em>[+]</em></p>
  </article>
  <div class="sep" style="top:194px"></div>
  <article class="post" style="top:209px">
    <div class="date"><b>FEB</b><strong>01</strong><span>2014</span></div>
    <h4>Lorem ipsum dolor sit amet...</h4>
    <p>Lorem Ipsum is simply dummy text of the printing and typesetting industry. <em>[+]</em></p>
  </article>
</section>

<footer class="site-footer">
  <h5 style="left:62px">Subscribe to<br>our newsletter</h5>
  <div class="field" style="top:79px">Enter Your Name</div>
  <div class="field" style="top:107px">Enter Your Email</div>
  <div class="subscribe">SUBSCRIBE</div>

  <h5 style="left:273px">Quick Links</h5>
  <ul class="links"><li>Home</li><li>Landing</li><li>Testimonials</li><li>Blog</li><li>Contact</li></ul>

  <h5 style="left:412px">Contact Info</h5>
  <div class="contact-item" style="top:59px">
    <svg width="9" height="11" viewBox="0 0 9 11" aria-hidden="true"><path d="M4.5 0.5 A4 4 0 0 1 8.5 4.5 C8.5 7 4.5 10.5 4.5 10.5 C4.5 10.5 0.5 7 0.5 4.5 A4 4 0 0 1 4.5 0.5Z" fill="#b9b9b9"/><circle cx="4.5" cy="4.5" r="1.5" fill="#333"/></svg>
    <span>228, lorem ipsum dolor sit,<br>dosis miunf- 845848</span></div>
  <div class="contact-item" style="top:97px">
    <svg width="10" height="10" viewBox="0 0 10 10" aria-hidden="true"><path d="M2 0.5 L4 2.8 L3 4 C3.6 5.3 4.7 6.4 6 7 L7.2 6 L9.5 8 L8 9.5 C4 9 1 6 0.5 2Z" fill="#b9b9b9"/></svg>
    <span>Phone: (800)555-20-4417<br>Fax: (800)555-20-4418</span></div>
  <div class="contact-item" style="top:133px">
    <svg width="10" height="9" viewBox="0 0 10 9" aria-hidden="true"><path d="M0.5 3.5 L5 0.5 L9.5 3.5 V8.5 H0.5Z" fill="#b9b9b9"/><path d="M0.5 3.5 L5 6 L9.5 3.5" fill="none" stroke="#333" stroke-width=".8"/></svg>
    <span>Email: info@brightlineweb.nl<br>Website:www.brightlineweb.nl</span></div>

  <h5 style="left:594px">Stay Connected</h5>
  <div class="social" style="top:58px"><i></i>Follow Us On Friendbook</div>
  <div class="social" style="top:90px"><i></i>Follow Us On Chirper</div>
  <div class="social" style="top:122px"><i></i>Follow Us On ProLink</div>
</footer>

<div class="legal">© 2015 Brightline All Rights Reserved.<br>Terms of Use | Legal Disclaimer | Privacy Policy | References</div>

</body>
</html>
```